Whitcombe Business Card Design

The name of the business is Dario Whitcombe, CPA LLC
The service that we offer is Accounting, Tax & Consulting Services. I need it to have the following items:
Dario Whitcombe, Principal
Phone Number
Email Address
Physical Address

I have attached the company logo, one in black and one in white. Please provide a design in black background and the other in white background. Please include "Accounting, Tax & Consulting Services". I want the business card to be clean and very professional.

```html
<!DOCTYPE html>
<html lang="en">
<head>
<meta charset="utf-8">
<title>Dario Whitcombe, CPA LLC — Business Cards</title>
<link rel="stylesheet" href="https://fonts.googleapis.com/css2?family=Source+Sans+3:wght@400;600&display=swap">
<style>
  :root {
    --page-bg: #1f1f20;
    --card-light: #ececec;
    --card-dark: #3b3c3e;
    --brand-red: #9a1c1f;
    --ink-dark: #3a3b3d;
    --ink-mid: #555658;
    --ink-white: #ffffff;
    --font-main: "Source Sans 3", "Helvetica Neue", Arial, sans-serif;
  }
  * { box-sizing: border-box; margin: 0; padding: 0; }
  html, body {
    width: 1200px; height: 1200px; overflow: hidden;
    background: var(--page-bg);
    font-family: var(--font-main);
  }
  .canvas { position: relative; width: 1200px; height: 1200px; }

  .card {
    position: absolute;
    left: 228px;
    width: 745px;
    height: 428px;
    overflow: hidden;
  }
  .card--front { top: 170px; background: var(--card-light); }
  .card--back  { top: 640px; background: var(--card-dark); }

  /* Front card */
  .brand-block {
    position: absolute; left: 0; width: 352px; top: 136px;
    display: flex; flex-direction: column; align-items: center; gap: 16px;
  }
  .brand-block__square { width: 44px; height: 44px; background: var(--brand-red); }
  .brand-block__name {
    font-size: 19px; font-weight: 600; letter-spacing: 0.5px;
    color: var(--ink-dark); text-transform: uppercase; white-space: nowrap;
  }

  .person { position: absolute; left: 456px; top: 50px; }
  .person__name {
    font-size: 25px; font-weight: 400; letter-spacing: 0.3px;
    text-transform: uppercase; color: var(--ink-dark); line-height: 1;
  }
  .person__first { color: var(--brand-red); }
  .person__role { margin-top: 8px; font-size: 16px; color: var(--ink-mid); }
  .person__rule {
    position: absolute; left: 456px; right: 0; top: 122px;
    height: 1px; background: var(--brand-red);
  }

  .address {
    position: absolute; left: 456px; top: 208px;
    font-size: 16px; line-height: 26px; color: var(--brand-red);
  }
  .contacts { position: absolute; left: 462px; top: 266px; list-style: none; }
  .contacts__item {
    display: flex; align-items: center; height: 25px;
    font-size: 15.5px; color: var(--ink-mid);
  }
  .contacts__icon { width: 12px; height: 12px; margin-right: 14px; fill: var(--brand-red); }

  .front-bands { position: absolute; left: 0; top: 0; width: 745px; height: 428px; }

  /* Back card */
  .back-brand {
    position: absolute; left: 0; right: 0; top: 176px;
    display: flex; justify-content: center; align-items: center; gap: 18px;
  }
  .back-brand__square { width: 40px; height: 40px; background: var(--ink-white); }
  .back-brand__name {
    font-size: 30px; font-weight: 400; letter-spacing: 0.6px;
    color: var(--ink-white); text-transform: uppercase; white-space: nowrap;
  }
  .service-band {
    position: absolute; left: 0; right: 0; top: 375px; height: 53px;
    background: var(--brand-red);
  }
  .service-tab {
    position: absolute; left: 117px; width: 492px; top: 345px; height: 60px;
    background: var(--brand-red); border-radius: 12px 12px 0 0;
    display: flex; justify-content: center; padding-top: 9px;
  }
  .service-tab__text { font-size: 24px; color: var(--ink-white); letter-spacing: 0.2px; }
</style>
</head>
<body>
<main class="canvas">

  <section class="card card--front" aria-label="Business card, front">
    <svg class="front-bands" viewBox="0 0 745 428" aria-hidden="true">
      <polygon points="0,368 285,368 353,428 0,428" fill="var(--brand-red)"/>
      <polygon points="304,385 581,385 581,414 337,414" fill="var(--ink-dark)"/>
      <rect x="685" y="385" width="60" height="29" fill="var(--ink-dark)"/>
    </svg>

    <div class="brand-block">
      <span class="brand-block__square"></span>
      <span class="brand-block__name">Dario Whitcombe, CPA LLC</span>
    </div>

    <div class="person">
      <h1 class="person__name"><span class="person__first">Dario</span> Whitcombe</h1>
      <p class="person__role">Principal</p>
    </div>
    <div class="person__rule"></div>

    <address class="address" style="font-style:normal">
      PO Box 2870 Larchmont<br>Calder, AB T4R 1K6
    </address>

    <ul class="contacts">
      <li class="contacts__item">
        <svg class="contacts__icon" viewBox="0 0 24 24" aria-hidden="true"><path d="M6.6 10.8a15.1 15.1 0 0 0 6.6 6.6l2.2-2.2c.3-.3.7-.4 1-.2 1.1.4 2.3.6 3.6.6.6 0 1 .4 1 1V20c0 .6-.4 1-1 1A17 17 0 0 1 3 4c0-.6.4-1 1-1h3.5c.6 0 1 .4 1 1 0 1.2.2 2.4.6 3.6.1.3 0 .7-.2 1z"/></svg>
        555 (0) 204 718 336
      </li>
      <li class="contacts__item">
        <svg class="contacts__icon" viewBox="0 0 24 24" aria-hidden="true"><path d="M2 5h20v14H2z M3 6l9 7 9-7" /><path d="M2 5l10 8 10-8v-0H2z" fill="var(--card-light)"/></svg>
        office@whitcombecpa.com
      </li>
      <li class="contacts__item">
        <svg class="contacts__icon" viewBox="0 0 24 24" aria-hidden="true"><circle cx="12" cy="12" r="10"/><path d="M2 12h20M12 2c3 3 3 17 0 20M12 2c-3 3-3 17 0 20" stroke="var(--card-light)" stroke-width="1.6" fill="none"/></svg>
        www.whitcombecpa.com
      </li>
    </ul>
  </section>

  <section class="card card--back" aria-label="Business card, back">
    <div class="back-brand">
      <span class="back-brand__square"></span>
      <span class="back-brand__name">Dario Whitcombe, CPA LLC</span>
    </div>
    <div class="service-band"></div>
    <div class="service-tab">
      <p class="service-tab__text">Accounting, Tax &amp; Consulting Services</p>
    </div>
  </section>

</main>
</body>
</html>
```